Crimson Ridge Footrace Co.

We need a website (wordpress) design for a new website that we will be launching. This is for a new trail racing series in Canada.
We recently had a logo designed so want to incorporate the colours of the logo on the website design. Especially the dark blue, green and orange.
Websites that we like for comparison of trail running race themes are:
https://www.mosslinerunning.com/
https://www.bramblestridecup.com/
http://www.quarrypathcircuit.ca/
https://www.cobaltcreekchase.com/
http://www.dunmoorrunningtour.com/

Target Market(s)

Outdoor trail runners

Coding

Coded - Design and coding required

Number of Pages Required

4 page

Font styles to use
Sans Serif

Colors
0255a3
33b8a4
f37122

Requirements
Must have
• There will be a main page with eye catching design noting what we do. Page 2 and 3 will be for each race in the series. Page 1 will be a specific race, and page 2 with be for another race. page 3 and 4 will be for future races that we add so that each race has their own page.
• Our races all take place in the mountains, so using graphics including mountains, rivers, trees is all a requirement for us.
• Our logo is attached, we want to use the colours of the logo in the website design.
Nice to have
• Outdoor theme is a nice to have. We like wood and earth tone colours, and pictures/graphics of runners and mountains and trees.
• There are 4 people involved in our organization. We'd like a photo and brief blurb of each of us, similar to how this website did their layout: https://www.mosslinerunning.com/

```html
<!DOCTYPE html>
<html lang="en">
<head>
<meta charset="utf-8">
<title>Crimson Ridge Footrace Co.</title>
<link rel="stylesheet" href="https://fonts.googleapis.com/css2?family=Montserrat:wght@400;600;700;800&family=Open+Sans:wght@400;600;700&display=swap">
<style>
:root{
  --blue:#0255a3;
  --teal:#33b8a4;
  --orange:#f37122;
  --earth:#2b221c;
  --earth-deep:#1e1814;
  --white:#ffffff;
  --muted:#cfc6bd;
  --line:#4a3d33;
}
*{box-sizing:border-box;margin:0;padding:0}
html,body{width:1200px;height:3700px;overflow:hidden}
body{background:var(--earth);color:var(--white);font-family:"Open Sans",Arial,sans-serif;position:relative}
.heading{font-family:"Montserrat",Arial,sans-serif;font-weight:700;text-transform:uppercase;letter-spacing:1px}
.section-title{text-align:center;font-size:38px}
.section-title::after{content:"";display:block;width:44px;height:4px;background:var(--orange);margin:18px auto 0}

/* header + hero */
.hero{position:absolute;left:0;top:0;width:1200px;height:760px;overflow:hidden}
.hero-photo{position:absolute;inset:0;background:linear-gradient(180deg,#f0b565 0%,#d98b45 22%,#8c6a45 42%,#3f4a2d 62%,#25301f 100%)}
.brand{position:absolute;left:130px;top:14px;width:140px;height:140px;border-radius:50%;background:var(--earth);display:flex;align-items:center;justify-content:center;text-align:center;padding:18px;font-family:"Montserrat",Arial,sans-serif;font-weight:700;font-size:15px;line-height:1.25;color:var(--white);text-transform:uppercase;z-index:2}
.main-nav{position:absolute;left:400px;top:42px;display:flex;align-items:center;gap:6px;z-index:2}
.main-nav a{color:var(--white);text-decoration:none;font-family:"Montserrat",Arial,sans-serif;font-size:17px;font-weight:600;padding:8px 18px}
.main-nav a.active{background:var(--orange)}
.main-nav svg{margin-left:14px}
.hero-text{position:absolute;left:0;right:0;top:318px;text-align:center}
.hero-title{font-size:60px;font-weight:800;letter-spacing:2px}
.hero-sub{font-size:22px;font-weight:600;margin-top:28px}
.play{position:absolute;left:564px;top:490px}
.slide-arrow{position:absolute;top:420px}
.slide-arrow.prev{left:34px}
.slide-arrow.next{right:34px}

/* events */
.events{position:absolute;left:0;top:760px;width:1200px;height:640px}
.events .section-title{margin-top:130px}
.event-row{position:absolute;top:1030px;left:0;width:1200px;display:flex;justify-content:center;gap:28px}
.events-track{position:absolute;left:92px;top:270px;width:1016px;display:flex;justify-content:space-between}
.event{width:190px;text-align:center}
.event-badge{width:180px;height:180px;margin:0 auto;border-radius:50%;background:var(--white);border:6px solid #d8d2cc;display:flex;align-items:center;justify-content:center;color:var(--earth);font-family:"Montserrat",Arial,sans-serif;font-weight:700;font-size:18px}
.event.current .event-badge{border-color:var(--orange)}
.event-caption{margin-top:30px;color:var(--orange);font-family:"Montserrat",Arial,sans-serif;font-size:14px;font-weight:600;text-transform:uppercase;line-height:1.5}
.events-pager{position:absolute;left:594px;top:556px;font-size:14px;color:var(--white)}
.events .slide-arrow{top:500px}

/* about */
.about{position:absolute;left:0;top:1400px;width:1200px;height:580px;display:flex}
.about-photo{width:600px;height:580px;background:linear-gradient(160deg,#f4d9a4 0%,#c69a5e 35%,#6d6a3e 65%,#3b3a24 100%)}
.about-panel{width:600px;height:580px;background:var(--blue);padding:86px 60px 0 60px}
.about-panel h2{font-size:40px}
.about-panel h2::after{content:"";display:block;width:44px;height:4px;background:var(--orange);margin-top:14px}
.about-lead{font-weight:700;font-size:17px;line-height:1.6;margin-top:30px}
.about-body{font-size:15px;line-height:1.7;margin-top:20px;color:#dfe8f4}
.btn-outline{display:inline-block;margin-top:30px;border:2px solid var(--white);color:var(--white);font-family:"Montserrat",Arial,sans-serif;font-weight:600;font-size:14px;padding:12px 22px;text-transform:uppercase}

/* team */
.team{position:absolute;left:0;top:1980px;width:1200px;height:880px}
.team .section-title{margin-top:124px}
.team-grid{position:absolute;left:100px;top:268px;width:1000px;display:grid;grid-template-columns:492px 492px;gap:20px 16px}
.member{display:flex;height:232px}
.member-info{width:276px;padding:24px 24px}
.member-info.orange{background:var(--orange)}
.member-info.teal{background:var(--teal)}
.member-photo{width:216px;background:linear-gradient(180deg,#d9d4cf,#a39d96)}
.member-name{font-family:"Montserrat",Arial,sans-serif;font-weight:700;font-size:19px}
.member-role{font-size:13px;margin-top:6px;opacity:.9}
.member-bio{font-size:13px;line-height:1.65;margin-top:16px}

/* contact */
.contact{position:absolute;left:0;top:2860px;width:1200px;height:540px}
.contact .section-title{margin-top:120px}
.contact-row{position:absolute;left:0;right:0;top:222px;display:flex;justify-content:center;gap:120px;font-size:15px}
.contact-item{display:flex;align-items:center;gap:14px}
.contact-item .ring{width:44px;height:44px;border-radius:50%;background:#4a3d33;display:flex;align-items:center;justify-content:center}
.contact-form{position:absolute;left:200px;top:310px;width:792px;display:flex;gap:16px}
.form-col{width:388px;display:flex;flex-direction:column;gap:12px}
.field{background:var(--white);color:#8a8a8a;font-size:14px;height:42px;padding:11px 16px}
.field.message{height:174px}
.btn-submit{position:absolute;left:880px;top:404px;background:var(--orange);color:var(--white);font-family:"Montserrat",Arial,sans-serif;font-weight:700;font-size:14px;padding:12px 28px;border-radius:22px;text-transform:uppercase}

/* footer */
.site-footer{position:absolute;left:0;top:3400px;width:1200px;height:300px;background:var(--earth-deep)}
.social{position:absolute;left:248px;top:116px;display:flex;gap:16px}
.social span{width:36px;height:36px;border-radius:50%;background:var(--white)}
.footer-nav{position:absolute;left:100px;top:190px;display:flex;gap:54px;font-family:"Montserrat",Arial,sans-serif;font-size:13px;text-transform:uppercase;color:var(--white)}
.copyright{position:absolute;left:100px;right:300px;top:236px;text-align:center;font-size:13px;color:var(--muted)}
.footer-brand{position:absolute;left:920px;top:82px;width:170px;height:170px;border-radius:50%;background:#3a2f27;display:flex;align-items:center;justify-content:center;text-align:center;padding:22px;font-family:"Montserrat",Arial,sans-serif;font-weight:700;font-size:17px;line-height:1.25;text-transform:uppercase}
</style>
</head>
<body>

<header class="hero">
  <div class="hero-photo" role="img" aria-label="Trail runner standing on a rocky summit above forested mountains at sunset"></div>
  <div class="brand">Crimson Ridge Footrace Co.</div>
  <nav class="main-nav">
    <a class="active">Home</a><a>About us</a><a>Services</a><a>Team</a><a>Events</a><a>Contact us</a>
    <svg width="20" height="20" viewBox="0 0 20 20" fill="none" stroke="#fff" stroke-width="2.5"><circle cx="8" cy="8" r="6"/><line x1="12.5" y1="12.5" x2="18" y2="18"/></svg>
  </nav>
  <div class="hero-text">
    <h1 class="heading hero-title">Crimson Ridge Footrace Co.</h1>
    <p class="hero-sub">Sed ut perspiciatis unde omnis iste natus error sit voluptatem accusantium doloremque</p>
  </div>
  <svg class="play" width="72" height="72" viewBox="0 0 72 72"><circle cx="36" cy="36" r="33" fill="none" stroke="#fff" stroke-width="4"/><polygon points="29,22 52,36 29,50" fill="#fff"/></svg>
  <svg class="slide-arrow prev" width="24" height="48" viewBox="0 0 24 48"><polyline points="20,4 4,24 20,44" fill="none" stroke="#fff" stroke-width="3"/></svg>
  <svg class="slide-arrow next" width="24" height="48" viewBox="0 0 24 48"><polyline points="4,4 20,24 4,44" fill="none" stroke="#fff" stroke-width="3"/></svg>
</header>

<section class="events">
  <h2 class="heading section-title">Latest Events</h2>
  <div class="events-track">
    <div class="event"><div class="event-badge">Tall Pine</div><p class="event-caption">Alder Creek Dash<br>May 12</p></div>
    <div class="event"><div class="event-badge">Summit Shop</div><p class="event-caption">Cedar Loop Ultra<br>June 9</p></div>
    <div class="event current"><div class="event-badge">Peak Lodge</div><p class="event-caption">Granite Steps 30K<br>July 14</p></div>
    <div class="event"><div class="event-badge">Mossy Trail</div><p class="event-caption">Riverbend Night Run<br>August 4</p></div>
    <div class="event"><div class="event-badge">North Fork</div><p class="event-caption">Larch Summit Climb<br>September 8</p></div>
  </div>
  <span class="events-pager">5</span>
  <svg class="slide-arrow prev" width="20" height="40" viewBox="0 0 20 40" style="top:370px"><polyline points="17,3 3,20 17,37" fill="none" stroke="#fff" stroke-width="3"/></svg>
  <svg class="slide-arrow next" width="20" height="40" viewBox="0 0 20 40" style="top:370px"><polyline points="3,3 17,20 3,37" fill="none" stroke="#fff" stroke-width="3"/></svg>
</section>

<section class="about">
  <div class="about-photo" role="img" aria-label="Woman running on a sunlit forest trail"></div>
  <div class="about-panel">
    <h2 class="heading">About Us</h2>
    <p class="about-lead">Trail races through the coastal mountains, along rivers and under old cedar, for runners of every pace.</p>
    <p class="about-body">We plan each course by foot, mark every junction and staff aid stations with volunteers who know the trail. Our series brings small local races together under one calendar, one set of standings and one season of shared finish lines. Come run with us.</p>
    <span class="btn-outline">Read more</span>
  </div>
</section>

<section class="team">
  <h2 class="heading section-title">Our Team</h2>
  <div class="team-grid">
    <article class="member">
      <div class="member-info orange"><h3 class="member-name">Alder Quinn</h3><p class="member-role">Race Director</p><p class="member-bio">Course builder and long-time ultra runner who scouts every route before race day and keeps the aid stations stocked.</p></div>
      <div class="member-photo" role="img" aria-label="Portrait photo of Alder Quinn"></div>
    </article>
    <article class="member">
      <div class="member-photo" role="img" aria-label="Portrait photo of Reid Calloway"></div>
      <div class="member-info teal"><h3 class="member-name">Reid Calloway</h3><p class="member-role">Timing Lead</p><p class="member-bio">Handles permits, timing and results, and still finds time to run the hills above the valley each morning.</p></div>
    </article>
    <article class="member">
      <div class="member-info teal"><h3 class="member-name">Nolan Vey</h3><p class="member-role">Course Marshal</p><p class="member-bio">Leads our volunteer crews, marks the courses with flagging tape and makes sure nobody takes a wrong turn.</p></div>
      <div class="member-photo" role="img" aria-label="Portrait photo of Nolan Vey"></div>
    </article>
    <article class="member">
      <div class="member-photo" role="img" aria-label="Portrait photo of Tessa Marlow"></div>
      <div class="member-info orange"><h3 class="member-name">Tessa Marlow</h3><p class="member-role">Runner Care</p><p class="member-bio">Runs registration and sponsor relations, and greets every runner at the finish line with a cold drink.</p></div>
    </article>
  </div>
</section>

<section class="contact">
  <h2 class="heading section-title">Get in Touch</h2>
  <div class="contact-row">
    <div class="contact-item"><span class="ring"><svg width="20" height="20" viewBox="0 0 24 24" fill="#fff"><path d="M6.6 10.8a15 15 0 0 0 6.6 6.6l2.2-2.2a1 1 0 0 1 1-.25 11.4 11.4 0 0 0 3.6.6 1 1 0 0 1 1 1V20a1 1 0 0 1-1 1A17 17 0 0 1 3 4a1 1 0 0 1 1-1h3.5a1 1 0 0 1 1 1c0 1.25.2 2.45.6 3.6a1 1 0 0 1-.25 1z"/></svg></span>Phone : 1 604 555 0172</div>
    <div class="contact-item"><span class="ring"><svg width="20" height="20" viewBox="0 0 24 24" fill="none" stroke="#fff" stroke-width="2"><rect x="3" y="5" width="18" height="14"/><polyline points="3,5 12,13 21,5"/></svg></span>Email : hello@crimsonridgefootrace.ca</div>
  </div>
  <div class="contact-form">
    <div class="form-col"><div class="field">Enter Name</div><div class="field">Enter Email</div><div class="field">Subject</div></div>
    <div class="form-col"><div class="field message">Message</div></div>
  </div>
  <span class="btn-submit">Submit</span>
</section>

<footer class="site-footer">
  <div class="social"><span></span><span></span><span></span><span></span><span></span><span></span></div>
  <nav class="footer-nav"><span>Home</span><span>About us</span><span>Services</span><span>Team</span><span>Events</span><span>Contact</span></nav>
  <p class="copyright">© Copyright 2025 Crimson Ridge Footrace Co. All rights reserved | Privacy Policy</p>
  <div class="footer-brand">Crimson Ridge Footrace Co.</div>
</footer>

</body>
</html>
```